Business Card Design

I need business cards designed for a new company i have started that makes cakes, particularly themed kids cakes with a really modern design and I would like to have my business cards reflect this. I have attached some photos of cakes I have made and would like some to be used.

Industry/Entity Type

Business

Contact Information for Business Card

Business Name: Tarts and Treats by Maren
Mobile: 0492 815 063
email: maren@tartsandtreatsbymaren.example.au
Instagram: instagram.com/tartsandtreatsbymaren/
Facebook: fb.me/tartsandtreatsbymaren

Colors
e667a6
b768aa
3276b5

Requirements
Must have
• Business Name: Tarts and Treats by Maren
• Mobile: 0492 815 063
• email: maren@tartsandtreatsbymaren.example.au
• Instagram: instagram.com/tartsandtreatsbymaren/
• Facebook: fb.me/tartsandtreatsbymaren
Nice to have
• 2 to 3 pictures of my cakes

```html
<!DOCTYPE html>
<html lang="en">
<head>
<meta charset="utf-8">
<title>Tarts and Treats by Maren – Business Card</title>
<link href="https://fonts.googleapis.com/css2?family=Open+Sans:wght@400;600;700&display=swap" rel="stylesheet">
<style>
  :root {
    --pink: #e667a6;
    --pink-deep: #d95a98;
    --pink-soft: #f08cbd;
    --mauve: #b768aa;
    --ink: #555558;
    --rule: #c9c9cc;
    --paper: #ffffff;
    --paper-shade: #f1f1f3;
    --backdrop: #ece8e4;
  }
  * { margin: 0; padding: 0; box-sizing: border-box; }
  html, body { width: 1200px; height: 843px; overflow: hidden; }
  body {
    background: var(--backdrop);
    font-family: "Open Sans", Arial, sans-serif;
    position: relative;
  }
  .card {
    position: absolute;
    width: 620px;
    height: 378px;
    border-radius: 3px;
    box-shadow: 0 10px 28px rgba(60, 40, 30, 0.25);
    overflow: hidden;
  }
  /* Back of card */
  .card-back {
    left: 70px;
    top: 60px;
    background: linear-gradient(120deg, var(--pink-deep) 0%, var(--pink) 55%, #c8558f 100%);
  }
  .card-back .glow-band {
    position: absolute;
    left: 200px;
    top: 0;
    width: 90px;
    height: 100%;
    background: linear-gradient(90deg, rgba(255,255,255,0) 0%, rgba(255,255,255,0.22) 50%, rgba(255,255,255,0) 100%);
  }
  .card-back .back-name {
    position: absolute;
    left: 0;
    right: 0;
    top: 168px;
    text-align: center;
    color: var(--paper);
    font-weight: 600;
    font-size: 30px;
    letter-spacing: 0.5px;
  }
  /* Front of card */
  .card-front {
    left: 510px;
    top: 405px;
    background: linear-gradient(160deg, var(--paper) 55%, var(--paper-shade) 100%);
  }
  .brand-name {
    position: absolute;
    left: 260px;
    top: 58px;
    width: 250px;
    color: var(--pink);
    font-weight: 600;
    font-size: 30px;
    line-height: 1.12;
    text-align: center;
  }
  .person {
    position: absolute;
    left: 70px;
    top: 212px;
    width: 170px;
    text-align: right;
  }
  .person-name {
    color: var(--pink);
    font-weight: 700;
    font-size: 19px;
    letter-spacing: 0.3px;
  }
  .person-title {
    color: var(--pink);
    font-size: 15px;
    margin-top: 2px;
  }
  .divider {
    position: absolute;
    left: 258px;
    top: 196px;
    width: 1px;
    height: 118px;
    background: var(--rule);
  }
  .contact-list {
    position: absolute;
    left: 274px;
    top: 200px;
    list-style: none;
  }
  .contact-item {
    display: flex;
    align-items: center;
    gap: 9px;
    height: 26px;
    color: var(--ink);
    font-size: 14px;
  }
  .contact-icon { width: 15px; height: 15px; flex: none; }
  .social-mark {
    width: 13px;
    height: 13px;
    margin: 0 1px;
    background: var(--pink);
    border-radius: 2px;
    flex: none;
  }
</style>
</head>
<body>
  <section class="card card-back" aria-label="Card back">
    <div class="glow-band"></div>
    <p class="back-name">Tarts and Treats by Maren</p>
  </section>

  <section class="card card-front" aria-label="Card front">
    <p class="brand-name">Tarts and Treats by Maren</p>

    <div class="person">
      <p class="person-name">MAREN ALDER</p>
      <p class="person-title">CEO/Founder</p>
    </div>

    <div class="divider"></div>

    <ul class="contact-list">
      <li class="contact-item">
        <svg class="contact-icon" viewBox="0 0 15 15" aria-hidden="true">
          <rect x="3.5" y="0.5" width="8" height="14" rx="1.5" fill="none" stroke="#e667a6" stroke-width="1.4"/>
          <rect x="5" y="2.5" width="5" height="8" fill="#e667a6"/>
          <circle cx="7.5" cy="12.3" r="0.9" fill="#e667a6"/>
        </svg>
        <span>0492 815 063</span>
      </li>
      <li class="contact-item">
        <svg class="contact-icon" viewBox="0 0 15 15" aria-hidden="true">
          <rect x="0.5" y="2.5" width="14" height="10" rx="1" fill="#e667a6"/>
          <path d="M1 3.2 L7.5 8.2 L14 3.2" fill="none" stroke="#fff" stroke-width="1.3"/>
        </svg>
        <span>maren@tartsandtreatsbymaren.example.au</span>
      </li>
      <li class="contact-item">
        <span class="social-mark" aria-hidden="true"></span>
        <span>tartsandtreatsbymaren</span>
      </li>
      <li class="contact-item">
        <span class="social-mark" aria-hidden="true"></span>
        <span>tartsandtreatsbymaren</span>
      </li>
    </ul>
  </section>
</body>
</html>
```